Coffeeshop menu for filter tip

We want to have a cannabis (coffeeshop) menu in the size 25mm wide x 60mm wide. Some examples attached.

it must have the following text:
Menu

WEED p/g
Oblivane €16
Cloudplum €14
Tide Runner €14
Quincefig €16
Mega Marsh €14
Grey Heron €14

HASH p/g
Tashar Amber €12
Pebble Frost€11
Lime Dunes €14
Ash Petal €10

Target Market(s)

tourist in Amsterdam

Requirements
Nice to have
• cannabis sign leaf
• No Cigarettes allowed symbol

```html
<!DOCTYPE html>
<html lang="en">
<head>
<meta charset="utf-8">
<title>Amsterdam Menu</title>
<link href="https://fonts.googleapis.com/css2?family=Bebas+Neue&family=Kaushan+Script&family=Alegreya:wght@400&family=Nunito+Sans:wght@400&display=swap" rel="stylesheet">
<style>
  :root {
    --backdrop: #1b1c1e;
    --paper: #ffffff;
    --leaf-pale: #b9e2bf;
    --leaf-light: #7fcf8c;
    --leaf-mid: #3fb85c;
    --leaf-deep: #1e9444;
    --mint-wash: #dcefe0;
    --accent-red: #e23e2b;
    --ink: #111111;
  }
  * { margin: 0; padding: 0; box-sizing: border-box; }
  html, body {
    width: 738px; height: 1200px; overflow: hidden;
    background: var(--backdrop);
  }
  .menu-card {
    position: absolute; left: 164px; top: 109px;
    width: 410px; height: 982px;
    background: var(--paper);
    overflow: hidden;
  }
  .leaf-frame { position: absolute; inset: 0; width: 410px; height: 982px; }
  .title-city {
    position: absolute; left: 0; width: 410px; top: 116px;
    text-align: center;
    font-family: "Kaushan Script", cursive;
    font-weight: 400; font-size: 32px; line-height: 44px;
    color: var(--accent-red);
  }
  .title-menu {
    position: absolute; left: 0; width: 410px; top: 160px;
    text-align: center;
    font-family: "Bebas Neue", sans-serif;
    font-weight: 400; font-size: 82px; line-height: 70px;
    color: var(--accent-red);
  }
  .section-heading {
    position: absolute; left: 96px;
    font-family: "Kaushan Script", cursive;
    font-weight: 400; font-size: 44px; line-height: 56px;
    color: var(--accent-red);
  }
  .unit-label {
    position: absolute; left: 284px;
    font-family: "Alegreya", serif;
    font-size: 23px; line-height: 28px; color: var(--ink);
  }
  .price-list { position: absolute; left: 107px; width: 230px; list-style: none; }
  .price-list li {
    display: flex; justify-content: space-between;
    height: 35.3px; line-height: 35.3px;
  }
  .strain { font-family: "Alegreya", serif; font-size: 21px; color: var(--ink); }
  .price { font-family: "Nunito Sans", sans-serif; font-size: 17px; color: var(--ink); width: 51px; }
  .weed-heading { top: 252px; }
  .weed-unit { top: 272px; }
  .weed-list { top: 314px; }
  .hash-heading { top: 552px; }
  .hash-unit { top: 576px; }
  .hash-list { top: 613px; }
  .notice {
    position: absolute; left: 127px; top: 782px;
    display: flex; align-items: center; gap: 8px;
    font-family: "Nunito Sans", sans-serif; font-size: 15px; color: var(--ink);
  }
</style>
</head>
<body>
  <main class="menu-card">
    <svg class="leaf-frame" viewBox="0 0 410 982" role="img" aria-label="Frame of green cannabis leaves around the menu edges">
      <defs>
        <radialGradient id="centreGlow" cx="0.6" cy="0.42" r="0.62">
          <stop offset="0.35" stop-color="#ffffff"/>
          <stop offset="0.7" stop-color="#e3f2e6"/>
          <stop offset="1" stop-color="#a8dbb1"/>
        </radialGradient>
        <linearGradient id="topBand" x1="0" y1="0" x2="0" y2="1">
          <stop offset="0" stop-color="#2fb24f" stop-opacity="0.85"/>
          <stop offset="0.6" stop-color="#8fd39a" stop-opacity="0.4"/>
          <stop offset="1" stop-color="#ffffff" stop-opacity="0"/>
        </linearGradient>
        <linearGradient id="bottomBand" x1="0" y1="1" x2="0" y2="0">
          <stop offset="0" stop-color="#3cb65a" stop-opacity="0.9"/>
          <stop offset="0.6" stop-color="#7fcf8c" stop-opacity="0.45"/>
          <stop offset="1" stop-color="#ffffff" stop-opacity="0"/>
        </linearGradient>
        <linearGradient id="leftBand" x1="0" y1="0" x2="1" y2="0">
          <stop offset="0" stop-color="#3fb85c" stop-opacity="0.85"/>
          <stop offset="0.6" stop-color="#8fd39a" stop-opacity="0.35"/>
          <stop offset="1" stop-color="#ffffff" stop-opacity="0"/>
        </linearGradient>
        <linearGradient id="rightBand" x1="1" y1="0" x2="0" y2="0">
          <stop offset="0" stop-color="#1e9444" stop-opacity="0.85"/>
          <stop offset="0.6" stop-color="#6cc67c" stop-opacity="0.35"/>
          <stop offset="1" stop-color="#ffffff" stop-opacity="0"/>
        </linearGradient>
      </defs>
      <rect x="0" y="0" width="410" height="982" fill="url(#centreGlow)"/>
      <rect x="0" y="0" width="410" height="120" fill="url(#topBand)"/>
      <rect x="0" y="840" width="410" height="142" fill="url(#bottomBand)"/>
      <rect x="0" y="0" width="95" height="982" fill="url(#leftBand)"/>
      <rect x="345" y="0" width="65" height="982" fill="url(#rightBand)"/>
    </svg>

    <p class="title-city">Amsterdam</p>
    <h1 class="title-menu">MENU</h1>

    <h2 class="section-heading weed-heading">Weed</h2>
    <span class="unit-label weed-unit">p/g</span>
    <ul class="price-list weed-list">
      <li><span class="strain">Oblivane</span><span class="price">€16</span></li>
      <li><span class="strain">Cloudplum</span><span class="price">€14</span></li>
      <li><span class="strain">Tide Runner</span><span class="price">€14</span></li>
      <li><span class="strain">Quincefig</span><span class="price">€16</span></li>
      <li><span class="strain">Mega Marsh</span><span class="price">€14</span></li>
      <li><span class="strain">Grey Heron</span><span class="price">€14</span></li>
    </ul>

    <h2 class="section-heading hash-heading">Hash</h2>
    <span class="unit-label hash-unit">p/g</span>
    <ul class="price-list hash-list">
      <li><span class="strain">Tashar Amber</span><span class="price">€12</span></li>
      <li><span class="strain">Pebble Frost</span><span class="price">€11</span></li>
      <li><span class="strain">Lime Dunes</span><span class="price">€14</span></li>
      <li><span class="strain">Ash Petal</span><span class="price">€10</span></li>
    </ul>

    <p class="notice">
      <svg width="36" height="36" viewBox="0 0 36 36" aria-hidden="true">
        <circle cx="18" cy="18" r="15.5" fill="#fff" stroke="var(--accent-red)" stroke-width="3"/>
        <rect x="8" y="19" width="18" height="4" fill="#222"/>
        <rect x="23" y="19" width="3" height="4" fill="#777"/>
        <path d="M27 17c0-3 2-3 2-6" fill="none" stroke="#222" stroke-width="1.3"/>
        <line x1="8" y1="8" x2="28" y2="28" stroke="var(--accent-red)" stroke-width="3"/>
      </svg>
      NO CIGARETTES
    </p>
  </main>
</body>
</html>
```